Oil Field Service company needs professional business cards

Looking to clean up our current company business cards and look a little more professional. Brenwick Casing Services is a US based company that services the oil field. We deal with engineers, managers and oil rigs....................................................................................................................................................................................................................................................................................................................................................................................................

Target Market(s)

Oil and Gas professionals

Industry/Entity Type

Oil And Gas

Contact Information for Business Card

See attached photo as example

Font styles to use
Sans Serif

Colors
ec1f27

Requirements
Must have
• Company Logo, Name, Title, Cell, Office, Fax, Email.
• See attached photo
Nice to have
• External CRT, Internal CRT, Casing Crews, Torque Turn, Laydown Machine
Should not have
• Do not introduce any new pictures and keep it professional looking

```html
<!DOCTYPE html>
<html lang="en">
<head>
<meta charset="utf-8">
<title>Brenwick Casing Services – Business Card</title>
<link rel="stylesheet" href="https://fonts.googleapis.com/css2?family=Oswald:wght@300;400;600&family=Roboto:wght@400&display=swap">
<style>
  :root {
    --page: #e8e8e8;
    --navy: #3d5263;
    --red: #ec1f27;
    --paper: #f7f7f7;
    --ink: #3a3a3a;
    --light: #e4e4e4;
  }
  * { margin: 0; padding: 0; box-sizing: border-box; }
  html, body { width: 1200px; height: 576px; overflow: hidden; background: var(--page); }
  .canvas { position: relative; width: 1200px; height: 576px; }

  .card {
    position: absolute; top: 139px; width: 484px; height: 292px;
    border-radius: 6px;
  }
  .card--front { left: 82px; background: var(--navy); }
  .card--back { left: 602px; width: 481px; background: var(--paper); }

  .brand { position: absolute; font-family: "Oswald", sans-serif; font-weight: 600; text-align: center; line-height: 1; }
  .brand__name { display: block; letter-spacing: 1px; }
  .brand__tag { display: block; letter-spacing: 3px; }

  .card--front .brand { left: 0; right: 0; top: 114px; color: var(--light); }
  .card--front .brand__name { font-size: 44px; }
  .card--front .brand__tag { font-size: 15px; margin-top: 10px; }

  .card--back .brand { left: 22px; top: 30px; width: 216px; color: var(--navy); }
  .card--back .brand__name { font-size: 36px; }
  .card--back .brand__tag { font-size: 12px; margin-top: 10px; letter-spacing: 2.5px; }

  .person { position: absolute; left: 27px; top: 159px; }
  .person__name { font-family: "Oswald", sans-serif; font-weight: 400; font-size: 22px; color: var(--red); line-height: 1.1; }
  .person__title { font-family: "Roboto", sans-serif; font-size: 11px; color: #555; margin-top: 3px; }

  .services { position: absolute; left: 27px; top: 230px; list-style: none;
    font-family: "Oswald", sans-serif; font-weight: 300; font-size: 11.5px; color: var(--ink); line-height: 16px; width: 220px; }
  .services li { display: inline-block; margin-right: 6px; }
  .services li::before { content: "»"; margin-right: 5px; }

  .contact { position: absolute; left: 284px; top: 169px; list-style: none;
    font-family: "Oswald", sans-serif; font-weight: 300; font-size: 11.5px; color: var(--ink); }
  .contact li { display: flex; align-items: center; height: 15.8px; }
  .contact svg { width: 9px; height: 9px; margin-right: 8px; fill: var(--red); flex: none; }
</style>
</head>
<body>
<div class="canvas">
  <section class="card card--front" aria-label="Card front">
    <div class="brand">
      <span class="brand__name">BRENWICK</span>
      <span class="brand__tag">CASING SERVICES</span>
    </div>
  </section>

  <section class="card card--back" aria-label="Card back">
    <div class="brand">
      <span class="brand__name">BRENWICK</span>
      <span class="brand__tag">CASING SERVICES</span>
    </div>

    <div class="person">
      <p class="person__name">Wade Hollister</p>
      <p class="person__title">Area Manager</p>
    </div>

    <ul class="services">
      <li>Laydown Machine</li><li>Casing Crew</li>
      <li>Mud Tool</li><li>Torque Turn</li>
    </ul>

    <ul class="contact">
      <li><svg viewBox="0 0 10 10"><path d="M2 0.5l2 2-1 1.2c.6 1.3 1.6 2.3 2.9 2.9l1.2-1 2 2-1.3 1.9C3.8 9.3.7 6.2.1 1.8z"/></svg>(555) 214-6800</li>
      <li><svg viewBox="0 0 10 10"><path d="M0 3.2C2.5.8 7.5.8 10 3.2L9 4.6 7.3 4V3c-1.5-.5-3.1-.5-4.6 0v1L1 4.6zM2 5.5h6L9 10H1z"/></svg>(555) 318-4270</li>
      <li><svg viewBox="0 0 10 10"><path d="M2.5 0h5v3h-5zM0 3.5h10V8H8V6H2v2H0zM2.5 6.5h5V10h-5z"/></svg>(555) 214-6810</li>
      <li><svg viewBox="0 0 10 10"><path d="M5 0a3.5 3.5 0 0 1 3.5 3.5C8.5 6 5 10 5 10S1.5 6 1.5 3.5A3.5 3.5 0 0 1 5 0zm0 2a1.5 1.5 0 1 0 0 3 1.5 1.5 0 0 0 0-3z"/></svg>Redfield, OK 73990</li>
      <li><svg viewBox="0 0 10 10"><path d="M0 2h10L5 5.5zM0 3.2l5 3.5 5-3.5V8H0z"/></svg>wadehollister@brenwicksrvs.com</li>
      <li><svg viewBox="0 0 10 10"><path d="M5 .5a4.5 4.5 0 1 0 0 9 4.5 4.5 0 0 0 0-9zm0 1.2c.5.6.9 1.6 1 2.8H4c.1-1.2.5-2.2 1-2.8zM1.8 5.5H4c.1 1.2.5 2.2 1 2.8-1.6-.1-2.9-1.3-3.2-2.8zm4.2 0h2.2c-.3 1.5-1.6 2.7-3.2 2.8.5-.6.9-1.6 1-2.8zM1.8 4.5C2 3.3 3 2.2 4.2 1.9 3.8 2.6 3.6 3.5 3.5 4.5zm4.7 0c-.1-1-.3-1.9-.7-2.6C7 2.2 8 3.3 8.2 4.5z"/></svg>www.brenwicksrvs.com</li>
    </ul>
  </section>
</div>
</body>
</html>
```